U.S. Popcorn company needs business cards

We are a popcorn company that manufactures popcorn and sells it to grocery stores worldwide. Our theme is "Americana" and our logo is U.S. route 66 which is the most famous highway in the U.S.

We would like the design to be simple and to use both sides. On the back side we would like to see just the logo and website. The front would be normal details

Target Market(s)

Wholesalers, grocers and distributors

Industry/Entity Type

Manufacture

Contact Information for Business Card

Business name: Prairie Lantern Popcorn
Phone: +1 555 308 4726
Email: Dale@prairielanternpopcorn.com
website: www.prairielanternpopcorn.com
Tag Line: "POPular for a reason"
Name: Dale Whitcombe
Title: Founder/President

Requirements
Must have
• Either this design should be fun or clean and simple. I will let you show me your thougths.
Nice to have
• Anything that ties in the real Hwy Route 66.
• Colors might need to be red, white and blue incorporated.
Should not have
• Not be too busy.

```html
<!DOCTYPE html>
<html lang="en">
<head>
<meta charset="utf-8">
<title>Prairie Lantern Popcorn – Business Cards</title>
<link rel="stylesheet" href="https://fonts.googleapis.com/css2?family=Open+Sans:wght@400;600;700&display=swap">
<style>
  :root {
    --bg-top: #8c8c8c;
    --bg-bottom: #6f6f6f;
    --navy: #0d2a6a;
    --navy-card: #06296b;
    --white: #ffffff;
    --text-dark: #1d2a4a;
    --rule: #b9c0cc;
  }
  * { margin: 0; padding: 0; box-sizing: border-box; }
  html, body {
    width: 1200px; height: 900px; overflow: hidden;
  }
  body {
    position: relative;
    background: linear-gradient(180deg, var(--bg-top), var(--bg-bottom));
    font-family: "Open Sans", Arial, sans-serif;
  }
  .card {
    position: absolute;
    top: 306px;
    width: 440px;
    height: 271px;
    border-radius: 10px;
  }
  .card--front { left: 149px; background: var(--white); }
  .card--back { left: 608px; background: var(--navy-card); }

  .brand-name {
    position: absolute;
    font-weight: 700;
    text-transform: uppercase;
    text-align: center;
    line-height: 1.1;
    letter-spacing: 0.5px;
  }
  .card--front .brand-name {
    left: 40px; top: 82px; width: 140px;
    font-size: 18px;
    color: var(--navy);
  }
  .card--back .brand-name {
    left: 0; right: 0; top: 84px;
    font-size: 28px;
    color: var(--white);
  }

  .holder {
    position: absolute;
    left: 219px; top: 80px;
    color: var(--navy);
  }
  .holder__name { font-size: 15px; font-weight: 700; line-height: 18px; }
  .holder__title { font-size: 11.5px; color: var(--text-dark); line-height: 15px; }

  .contacts {
    position: absolute;
    left: 219px; top: 132px;
    list-style: none;
    font-size: 11.5px;
    color: var(--text-dark);
  }
  .contacts li {
    display: flex; align-items: center;
    height: 16px;
  }
  .contacts svg { width: 9px; height: 9px; margin-right: 7px; fill: var(--navy); }

  .tagline {
    position: absolute;
    left: 0; right: 0; top: 231px;
    display: flex; align-items: center;
    gap: 10px;
    font-size: 13px;
    color: var(--navy);
    white-space: nowrap;
  }
  .tagline::before, .tagline::after {
    content: ""; flex: 1; height: 1px; background: var(--rule);
  }
</style>
</head>
<body>
  <section class="card card--front">
    <div class="brand-name">Prairie Lantern Popcorn</div>

    <div class="holder">
      <div class="holder__name">Dale Whitcombe</div>
      <div class="holder__title">Founder/President</div>
    </div>

    <ul class="contacts">
      <li>
        <svg viewBox="0 0 10 10"><path d="M2 0.5l2 2-1 1.2c.6 1.3 1.6 2.3 2.9 2.9L7 5.5l2.5 2-1 2C4.5 9.6.4 5.5.5 1.5z"/></svg>
        +1 555 308 4726
      </li>
      <li>
        <svg viewBox="0 0 10 10"><path d="M0 2h10v6H0z M0 2l5 3.5L10 2" /></svg>
        Dale@prairielanternpopcorn.com
      </li>
      <li>
        <svg viewBox="0 0 10 10"><circle cx="5" cy="5" r="4.8"/></svg>
        www.prairielanternpopcorn.com
      </li>
    </ul>

    <div class="tagline">POPULAR FOR A REASON</div>
  </section>

  <section class="card card--back">
    <div class="brand-name">Prairie Lantern<br>Popcorn</div>
  </section>
</body>
</html>
```